BildeVOLD buisnesscard

Hey :) I need a modern buisnesscard for my company BildeVOLD
It most have:
Dagligleder og Fotograf: Henrik Audun Strandvik

Mob: +4791264085
Epost: post@bildevold.example
Adresse: Kvernbakken9, 6040 Nordvikstrand

Facbook and instagram logo with text BildeVOLD

BildeVOLD logo

It Company

```html
<!DOCTYPE html>
<html lang="no">
<head>
<meta charset="utf-8">
<title>BildeVOLD – visittkort</title>
<link href="https://fonts.googleapis.com/css2?family=Noto+Sans:wght@400;700&display=swap" rel="stylesheet">
<style>
  :root {
    --page: #e6e6e6;
    --card: #262626;
    --band: #a8a8a8;
    --ink-dark: #2b2b2b;
    --ink-light: #a3a3a3;
    --brand: #a8a8a8;
  }
  * { margin: 0; padding: 0; box-sizing: border-box; }
  html, body {
    width: 1200px; height: 1200px; overflow: hidden;
    background: var(--page);
    font-family: "Noto Sans", Verdana, sans-serif;
  }
  .card {
    position: absolute;
    left: 240px;
    width: 720px;
    height: 434px;
    background: var(--card);
  }
  .card--front { top: 106px; }
  .card--back { top: 624px; }

  .front__band {
    position: absolute;
    left: 0; top: 45px;
    width: 100%; height: 90px;
    background: var(--band);
  }
  .front__brand {
    position: absolute;
    left: 46px; top: 144px;
    font-size: 42px;
    font-weight: 700;
    line-height: 1;
    color: var(--brand);
    letter-spacing: 0.5px;
  }
  .front__person {
    position: absolute;
    right: 36px; top: 64px;
    text-align: right;
    color: var(--ink-dark);
  }
  .front__name { font-size: 24px; line-height: 1.1; letter-spacing: 0.5px; }
  .front__role { font-size: 14px; margin-top: 6px; letter-spacing: 0.3px; }

  .front__contact {
    position: absolute;
    left: 0; right: 0; top: 336px;
    text-align: center;
    color: var(--ink-light);
    font-size: 16px;
    letter-spacing: 0.4px;
    line-height: 30px;
  }

  .back__brand {
    position: absolute;
    left: 0; right: 0; top: 186px;
    text-align: center;
    font-size: 52px;
    font-weight: 700;
    line-height: 1;
    color: var(--brand);
  }
  .back__social {
    position: absolute;
    left: 0; right: 0; top: 335px;
    display: flex;
    justify-content: center;
    gap: 22px;
    color: var(--ink-light);
    font-size: 17px;
    letter-spacing: 0.4px;
  }
  .social-handle { display: flex; align-items: center; gap: 12px; }
  .social-handle__dot {
    width: 31px; height: 31px;
    border: 2px solid var(--ink-light);
    border-radius: 50%;
  }
</style>
</head>
<body>
  <section class="card card--front">
    <div class="front__band"></div>
    <div class="front__brand">BildeVOLD</div>
    <div class="front__person">
      <div class="front__name">Henrik Audun Strandvik</div>
      <div class="front__role">Dagligleder og Fotograf</div>
    </div>
    <div class="front__contact">
      <div>Kvernbakken9, 6040 Nordvikstrand</div>
      <div>M: 913 264 0857 | post@bildevold.example | www.bildevold.example</div>
    </div>
  </section>

  <section class="card card--back">
    <div class="back__brand">BildeVOLD</div>
    <div class="back__social">
      <div class="social-handle"><span class="social-handle__dot"></span>BildeVOLD</div>
      <div class="social-handle"><span class="social-handle__dot"></span>BildeVOLD</div>
    </div>
  </section>
</body>
</html>
```